Dentistry

Dentist's personal business card. No logo needed. The card shoul deliver the massage of reliability, professionalism, experience.
Please ad the full brief of the project: down the line it says: the winning look should be precise and pristine NO pictures of Teeth, smiles, instruments etc.

The details to be desplaid are:
Dr. Rob Tavolen
Doctor of Dental Surgery
PHD
Web. Www.drtavolen.com
Email. Rob@drtavolen.com
Tel 07742318590
Surgery address. 27Bferndale road London SW4 8QT UK
62 Wexley Row London SW3 2HN. Uk

Reason: Decided to make the payment unrefundable in order to get more designers involved.

Requirements
Should not have
• Logo, teeth, smile any sort of instruments.

```html
<!DOCTYPE html>
<html lang="en">
<head>
<meta charset="utf-8">
<title>Family Dentist – Business Card</title>
<link rel="stylesheet" href="https://fonts.googleapis.com/css2?family=Josefin+Sans:wght@300;400;600&display=swap">
<style>
  :root {
    --page-bg: #e9e6e1;
    --card-bg: #ffffff;
    --ink: #111111;
    --bar: #000000;
    --muted: #b5b5b5;
    --card-edge: #d8d4cd;
  }
  * { margin: 0; padding: 0; box-sizing: border-box; }
  html, body {
    width: 1200px;
    height: 1000px;
    overflow: hidden;
    background: var(--page-bg);
    font-family: "Josefin Sans", sans-serif;
    color: var(--ink);
  }
  .canvas { position: relative; width: 1200px; height: 1000px; }

  .card {
    position: absolute;
    width: 577px;
    height: 314px;
    background: var(--card-bg);
    border: 1px solid var(--card-edge);
    box-shadow: 0 4px 10px rgba(0, 0, 0, 0.12);
  }
  .card--front { left: 33px; top: 33px; }
  .card--back  { left: 573px; top: 257px; }

  .band {
    position: absolute;
    top: 143px;
    height: 38px;
    background: var(--bar);
  }
  .card--front .band { left: 0; width: 263px; }
  .card--back .band  { right: 0; width: 241px; }

  .title {
    position: absolute;
    left: 282px;
    top: 143px;
    font-weight: 300;
    font-size: 22px;
    letter-spacing: 1px;
    line-height: 1;
    color: var(--ink);
  }
  .name {
    position: absolute;
    left: 280px;
    top: 169px;
    font-weight: 400;
    font-size: 13px;
    letter-spacing: 1.4px;
    color: var(--muted);
    line-height: 1;
  }

  .address {
    position: absolute;
    right: 259px;
    top: 145px;
    text-align: right;
    font-style: normal;
    font-weight: 600;
    font-size: 12.5px;
    line-height: 18px;
    letter-spacing: 0.3px;
    white-space: nowrap;
  }

  .contact {
    position: absolute;
    top: 292px;
    font-size: 11.5px;
    font-weight: 400;
    letter-spacing: 0.4px;
    line-height: 1;
    white-space: nowrap;
  }
  .contact--phone { left: 33px; }
  .contact--email { left: 224px; }
  .contact--web   { left: 435px; }
</style>
</head>
<body>
  <main class="canvas">
    <section class="card card--front" aria-label="Card front">
      <div class="band"></div>
      <h1 class="title">FAMILY DENTIST</h1>
      <p class="name">JANE ROWE</p>
    </section>

    <section class="card card--back" aria-label="Card back">
      <address class="address">
        4417 Harbor Lane Fairview, CA 90000<br>
        4417 Harbor Lane Fairview, CA 90000
      </address>
      <div class="band"></div>
      <p class="contact contact--phone">8444 777 444</p>
      <p class="contact contact--email">office@rowedental.com</p>
      <p class="contact contact--web">www.rowedental.com</p>
    </section>
  </main>
</body>
</html>
```